Indy Film Production Company/Studio

We need a business card designed from an existing logo. We are a digital studio/production company that caters to creating genre entertainment, like Action, Horror, and martial arts. The card along with the logo will be used to Brand the company from letter heads to banners. The design will also be used for postcards and Brochures. It should be professional and masculine.
Updates

Thank you to all the designers who have participated. I'm narrowing down who it will be. Thank you again.

Target Market(s)

Investors, Networks, Producers, and actors

Industry/Entity Type

Film Production

Contact Information for Business Card

Teodoro Valbuena
Producer/Writer/Director
www.kestrelpicturehouse.example

Requirements
Must have
• Website address, Facebook icon and Twitter icon possibly in the back of the card.
Nice to have
• Logline of Company: Follow The Action.

```html
<!DOCTYPE html>
<html lang="en">
<head>
<meta charset="utf-8">
<title>Kestrel Picture House – Business Card</title>
<link rel="stylesheet" href="https://fonts.googleapis.com/css2?family=Montserrat:wght@400;500;800&display=swap">
<style>
  :root {
    --backdrop: #2a2a2a;
    --card-black: #000000;
    --accent-red: #e41f2b;
    --white: #ffffff;
    --emblem-grey: #3a3a3a;
  }
  * { margin: 0; padding: 0; box-sizing: border-box; }
  html, body {
    width: 1200px; height: 900px; overflow: hidden;
    background: var(--backdrop);
    font-family: "Montserrat", Arial, sans-serif;
  }
  .canvas { position: relative; width: 1200px; height: 900px; }
  .card {
    position: absolute; left: 250px;
    width: 700px; height: 400px;
    background: var(--card-black);
    overflow: hidden;
    box-shadow: 0 10px 30px rgba(0,0,0,.5);
  }
  .card--front { top: 40px; }
  .card--back { top: 460px; }
  .card__swoosh { position: absolute; inset: 0; width: 100%; height: 100%; }

  .wordmark {
    position: absolute;
    color: var(--white);
    font-weight: 800;
    text-transform: uppercase;
    line-height: 1;
  }
  .wordmark__main { display: block; font-size: 74px; letter-spacing: 2px; }
  .wordmark__sub { display: block; font-size: 25px; letter-spacing: 3px; margin-top: 6px; }
  .card--front .wordmark { left: 150px; top: 135px; }
  .card--back .wordmark { left: 150px; top: 262px; }
  .card--back .wordmark__main { font-size: 58px; }
  .card--back .wordmark__sub { font-size: 19px; letter-spacing: 2.5px; }

  .front-web {
    position: absolute; right: 28px; bottom: 26px;
    color: var(--white); font-size: 17px; font-weight: 400; letter-spacing: .5px;
  }
  .front-web .accent { color: var(--accent-red); }

  .contact {
    position: absolute; right: 130px; top: 30px;
    text-align: right; color: var(--white);
  }
  .contact__name {
    color: var(--accent-red); font-weight: 500; font-size: 21px; letter-spacing: 1.5px;
    text-transform: uppercase;
  }
  .contact__role {
    font-size: 13px; letter-spacing: 1.5px; text-transform: uppercase; margin-top: 3px;
  }
  .contact__list { list-style: none; margin-top: 20px; font-size: 14px; line-height: 1.5; }
  .contact__list li { display: flex; justify-content: flex-end; align-items: center; gap: 8px; }
  .contact__icon { width: 12px; height: 12px; flex: none; }
  .contact__social { margin-top: 6px; }
  .social-badge {
    display: inline-block; width: 14px; height: 14px; border-radius: 50%;
    background: var(--accent-red);
  }

  .sight-emblem {
    position: absolute; left: 70px; top: 175px;
    width: 100px; height: 100px; border-radius: 50%;
    background: radial-gradient(circle, var(--emblem-grey) 0%, rgba(58,58,58,0) 70%);
  }
</style>
</head>
<body>
<main class="canvas">

  <section class="card card--front" aria-label="Card front">
    <svg class="card__swoosh" viewBox="0 0 700 400" preserveAspectRatio="none" aria-hidden="true">
      <path d="M225 0 Q 560 15 700 185 L700 0 Z" fill="var(--white)"/>
      <path d="M300 0 Q 585 10 700 140 L700 0 Z" fill="var(--accent-red)"/>
    </svg>
    <div class="wordmark">
      <span class="wordmark__main">Kestrel</span>
      <span class="wordmark__sub">Picture House</span>
    </div>
    <p class="front-web">www.<span class="accent">kestrelpicturehouse</span>.example</p>
  </section>

  <section class="card card--back" aria-label="Card back">
    <svg class="card__swoosh" viewBox="0 0 700 400" preserveAspectRatio="none" aria-hidden="true">
      <path d="M590 0 Q 720 230 430 400 L700 400 L700 0 Z" fill="var(--white)"/>
      <path d="M640 0 Q 745 250 500 400 L700 400 L700 0 Z" fill="var(--accent-red)"/>
    </svg>

    <div class="sight-emblem" role="img" aria-label="Target sight emblem"></div>

    <div class="contact">
      <p class="contact__name">Teodoro Valbuena</p>
      <p class="contact__role">Producer / Writer / Director</p>
      <ul class="contact__list">
        <li>+330 2460-0147
          <svg class="contact__icon" viewBox="0 0 12 12" aria-hidden="true"><path d="M2.5 1 L4.5 1 L5.3 3.4 L4 4.4 Q5 6.8 7.6 8 L8.6 6.7 L11 7.5 L11 9.5 Q10.5 11 9 11 Q1 10 1 3 Q1 1.5 2.5 1 Z" fill="var(--accent-red)"/></svg>
        </li>
        <li>info@kestrelpicturehouse.example
          <svg class="contact__icon" viewBox="0 0 12 12" aria-hidden="true"><rect x="1" y="2.5" width="10" height="7" fill="none" stroke="var(--accent-red)" stroke-width="1.4"/><path d="M1 2.5 L6 6.5 L11 2.5" fill="none" stroke="var(--accent-red)" stroke-width="1.4"/></svg>
        </li>
        <li>www.kestrelpicturehouse.example
          <svg class="contact__icon" viewBox="0 0 12 12" aria-hidden="true"><circle cx="6" cy="6" r="5" fill="var(--accent-red)"/><path d="M1 6 H11 M6 1 Q3 6 6 11 M6 1 Q9 6 6 11" fill="none" stroke="var(--card-black)" stroke-width=".8"/></svg>
        </li>
        <li class="contact__social">
          <span class="social-badge" role="img" aria-label="Social network page"></span>
          <span class="social-badge" role="img" aria-label="Social network feed"></span>
        </li>
      </ul>
    </div>

    <div class="wordmark">
      <span class="wordmark__main">Kestrel</span>
      <span class="wordmark__sub">Picture House</span>
    </div>
  </section>

</main>
</body>
</html>
```